Graphic Design Project

We make rose petal jelly from old fashioned english roses. The jelly is sweet eaten with scones and clotted cream or as a filling in a victoria sandwich, as a topping on ice cream or thick set yogurt.
The image of the product is luxurious and decadent and very english.
We need a design for a label which has a picture of an old fashioned rose (rosa mundi or a compte de chambard) The rose must stand out clearly so the jelly is not confused with other fruit jams. The overall colour of the label should be pink and soft, with white or dark pink writing. The label needs to be fridge proof.

We also need a security strip to fit on the lid of the jar.

We need the following information on the label.
Name of our company-"Meadow Crown"
Name of Product-"Rose Petal Jelly"
Sales pitch-"With whole petals-a taste of summer, delicious on scones, as a filling in sponge cake, as a topping on ice cream or yogurt."
INGREDIENTS: Sugar, water, rose petals, lemon juice, natural jelling agent (agar-agar)
STORAGE: Store in a cool dry place, once opened keep refrigerated and consume within 4 weeks.
BEST BEFORE: See base

200g
Produced by:
MEADOW CROWN
The Larches
Pardew Lane
Ashcombe
Wyndshire
GL17 4RX
The label must have room for a bar code. The size of label approx 8-10cm long 5cm wide.
Updates

Hi

Just been looking at the Hartwell and Brace site and the labels they have there have the up market feel I am trying to convey. Hope that helps, its classy but not twee.

Thanks

Thanks for all submissions. I would be grateful if you googled images for 'Colourful and expensive biscuits at Hartwell Brace' The designs on the tins are the image we are trying to create. The colours are quite strong.

Thanks

Target Market(s)

older well off people who visit garden centres

Industry/Entity Type

Security

Requirements
Must have
• All writen info above and picture of old fashioned rose prferably rose a mundi. Luxury feel, very english, to appeal to older market
Pink colour sheme
Should not have
• dark or manly colours

```html
<!DOCTYPE html>
<html lang="en">
<head>
<meta charset="utf-8">
<title>Meadow Crown – Rose Petal Jelly Label</title>
<link rel="stylesheet" href="https://fonts.googleapis.com/css2?family=Tinos&family=Cormorant+Garamond:wght@600&family=Arimo&display=swap">
<style>
  :root {
    --label-pink: #fbeaf0;
    --frame-grey: #6f6f6f;
    --ink: #2e2e2e;
    --brand-grey: #6a6a6a;
    --title-pink: #e3178a;
    --rose-dark: #2f3140;
    --rose-light: #d9d6dc;
    --white: #ffffff;
  }
  * { margin: 0; padding: 0; box-sizing: border-box; }
  html, body { width: 1200px; height: 667px; overflow: hidden; }
  body { background: var(--label-pink); font-family: "Tinos", "Times New Roman", serif; color: var(--ink); }

  .label { position: relative; width: 1200px; height: 667px; background: var(--label-pink); }

  .frame { position: absolute; left: 0; top: 0; width: 1200px; height: 667px; }
  .frame path { fill: none; stroke: var(--frame-grey); stroke-width: 2.5; }

  .producer {
    position: absolute; left: 40px; top: 46px; height: 380px;
    writing-mode: vertical-rl; font-style: normal;
    font-size: 18.5px; line-height: 27px; color: var(--ink);
  }

  .barcode-space {
    position: absolute; left: 23px; top: 411px; width: 134px; height: 213px;
    background: var(--white);
    display: flex; align-items: center; justify-content: center;
  }
  .barcode-space span {
    writing-mode: vertical-rl;
    font-family: "Arimo", Arial, sans-serif; font-size: 21px; letter-spacing: 1px; color: var(--ink);
  }

  .centre-column { position: absolute; left: 251px; width: 752px; text-align: center; }

  .brand { top: 66px; font-size: 46px; font-style: normal; color: var(--brand-grey); letter-spacing: 1px; }

  .rose-art {
    position: absolute; left: 420px; top: 173px; width: 360px; height: 254px;
    border-radius: 48% 52% 44% 50% / 55% 50% 48% 45%;
    background: radial-gradient(ellipse at 45% 45%, var(--rose-light) 0%, #a9a6b0 38%, var(--rose-dark) 75%);
  }

  .weight { position: absolute; left: 776px; top: 390px; font-size: 19px; color: var(--ink); }

  .product-name {
    top: 430px; font-family: "Cormorant Garamond", "Times New Roman", serif; font-weight: 600;
    font-size: 68px; line-height: 80px; color: var(--title-pink);
  }

  .pitch { top: 528px; font-size: 21px; line-height: 35px; color: var(--ink); }

  .details {
    position: absolute; left: 1024px; top: 40px; height: 600px;
    writing-mode: vertical-rl; transform: rotate(180deg);
    font-size: 18px; line-height: 27px; color: var(--ink);
  }
</style>
</head>
<body>
<main class="label">
  <svg class="frame" viewBox="0 0 1200 667" aria-hidden="true">
    <path d="M281 29 H973 A30 30 0 0 0 1003 59 V610 A30 30 0 0 0 973 640 H281 A30 30 0 0 0 251 610 V59 A30 30 0 0 0 281 29 Z"/>
    <path d="M289 37 H965 A30 30 0 0 0 995 67 V602 A30 30 0 0 0 965 632 H289 A30 30 0 0 0 259 602 V67 A30 30 0 0 0 289 37 Z"/>
  </svg>

  <address class="producer">
    Produced by:<br>
    MEADOW CROWN<br>
    The Larches, Pardew Lane<br>
    Ashcombe, Wyndshire&nbsp; GL17 4RX
  </address>

  <div class="barcode-space"><span>BAR CODE</span></div>

  <div class="centre-column brand">Meadow Crown</div>

  <div class="rose-art" role="img" aria-label="Engraved illustration of old fashioned English roses with buds and leaves"></div>

  <div class="weight">200g</div>

  <h1 class="centre-column product-name">Rose Petal Jelly</h1>

  <p class="centre-column pitch">
    With whole petals-a taste of summer, delicious on scones,<br>
    as a filling in sponge cake, as a topping on ice cream or yogurt.
  </p>

  <p class="details">
    INGREDIENTS: Sugar, water, rose petals, lemon juice,<br>
    natural jelling agent (agar-agar)<br>
    STORAGE: Store in a cool dry place, once opened keep<br>
    refrigerated and consume within 4 weeks.<br>
    BEST BEFORE: See base
  </p>
</main>
</body>
</html>
```